BrivoTerna. Lantern of the Steady Harvest. Business card

Professional business card for BrivoTerna (Lantern of the Steady Harvest)
My rationale: Strategy-> Execution-> Results-> Value that lead to the BrivoTerna name: We put the Lantern of the Steady Harvest.
We deliver value to our customers helping them at defining a good strategy (cyan arrow). 90% of well formulated strategies fail due to poor execution so we also consider strategical execution very important (green arrow). Due to the execution we obtain the results (blue arrow). Finally, the results provide feedback to redefine strategy, and the new strategy has to be executed and new results obtained providing new feedback and on and on. It's like a wheel that finally, must create corporate value: value for shareholders, staholders, employees, providers...-

Target Market(s)

CEOs and steering comitees , invewrnent funds

Industry/Entity Type

Business Consultant

Contact Information for Business Card

Teodoro Vinsquel
CEO & Founder
teodoro.vinsquel@brivoterna-example.com
Mobile: +34 655.803.912
www.brivoterna-example.com

Colors

Designer to choose colors to be used in the design.

Requirements
Nice to have
• Nice to hace the words: Strategy, execution, results
• Nice to vave the claim: Lantern of the Steady Harvest
• The three colors should be shown:
• cyan for STRATEGY
• green for EXECUTION
• blue for RESULTS
Should not have
• Complete black background

```html
<!DOCTYPE html>
<html lang="en">
<head>
<meta charset="utf-8">
<title>BrivoTerna – Business Card</title>
<link href="https://fonts.googleapis.com/css2?family=Roboto:wght@400;500;700&display=swap" rel="stylesheet">
<style>
  :root {
    --backdrop: #9b9b9b;
    --brand-blue: #003399;
    --brand-blue-soft: #1c47a0;
    --brand-cyan: #00a6e6;
    --ink-blue: #1f3f99;
    --mist: #eef2f8;
    --paper: #ffffff;
  }
  html, body {
    margin: 0;
    width: 1200px;
    height: 900px;
    overflow: hidden;
    background: var(--backdrop);
    font-family: "Roboto", Arial, sans-serif;
  }
  .card {
    position: absolute;
    top: 214px;
    width: 270px;
    height: 474px;
    border-radius: 18px;
    overflow: hidden;
    box-shadow: -8px 10px 18px rgba(0, 0, 0, 0.35);
  }
  .card--back {
    left: 288px;
    background: var(--brand-blue);
  }
  .card--front {
    left: 641px;
    background: var(--paper);
  }
  .decor {
    position: absolute;
    z-index: 0;
  }
  .card--back .decor {
    left: 0;
    right: 0;
    top: 200px;
    bottom: 0;
    background: linear-gradient(200deg, rgba(28, 71, 160, 0) 15%, var(--brand-blue-soft) 60%, rgba(28, 71, 160, 0.6) 100%);
  }
  .card--front .decor {
    left: 0;
    right: 0;
    top: 86px;
    height: 270px;
    background: linear-gradient(200deg, rgba(238, 242, 248, 0) 10%, var(--mist) 50%, rgba(238, 242, 248, 0) 100%);
  }
  .brand-dot {
    position: absolute;
    z-index: 1;
    left: 50%;
    width: 44px;
    height: 44px;
    margin-left: -22px;
    border-radius: 50%;
    background: var(--brand-cyan);
  }
  .card--back .brand-dot { top: 76px; }
  .card--front .brand-dot { top: 72px; }
  .wordmark {
    position: absolute;
    z-index: 1;
    left: 0;
    right: 0;
    text-align: center;
    font-weight: 700;
    font-size: 42px;
    letter-spacing: -1.2px;
    line-height: 1;
    margin: 0;
  }
  .card--back .wordmark {
    top: 139px;
    color: var(--paper);
  }
  .card--front .wordmark {
    top: 126px;
    color: var(--brand-blue);
  }
  .contact {
    position: absolute;
    z-index: 1;
    left: 30px;
    top: 348px;
    color: var(--ink-blue);
  }
  .contact__name {
    margin: 0;
    font-weight: 500;
    font-size: 17px;
    color: var(--brand-cyan);
    line-height: 1.1;
  }
  .contact__role {
    margin: 1px 0 0;
    font-size: 12px;
    line-height: 1.2;
  }
  .contact__list {
    list-style: none;
    margin: 12px 0 0;
    padding: 0;
    font-size: 11px;
    line-height: 17.7px;
  }
  .contact__item {
    display: flex;
    align-items: center;
    gap: 5px;
    white-space: nowrap;
  }
  .contact__icon {
    width: 9px;
    height: 9px;
    flex: none;
    fill: var(--brand-cyan);
  }
</style>
</head>
<body>
  <section class="card card--back" aria-label="Card back">
    <div class="decor" role="img" aria-label="Large faint sweeping arrow decoration in lighter blue"></div>
    <span class="brand-dot" aria-hidden="true"></span>
    <p class="wordmark">BrivoTerna</p>
  </section>

  <section class="card card--front" aria-label="Card front">
    <div class="decor" role="img" aria-label="Large faint sweeping arrow decoration in pale blue, green and cyan"></div>
    <span class="brand-dot" aria-hidden="true"></span>
    <p class="wordmark">BrivoTerna</p>

    <div class="contact">
      <h1 class="contact__name">Teodoro Vinsquel</h1>
      <p class="contact__role">CEO &amp; Founder</p>
      <ul class="contact__list">
        <li class="contact__item">
          <svg class="contact__icon" viewBox="0 0 10 10" aria-hidden="true">
            <path d="M2 0.5 L3.6 2.6 L2.8 3.6 Q4 6 6.4 7.2 L7.4 6.4 L9.5 8 L8.6 9.4 Q4.5 9.6 1.8 6.6 Q0.2 4.2 0.6 1.4 Z"/>
          </svg>
          +34 655.803.912
        </li>
        <li class="contact__item">
          <svg class="contact__icon" viewBox="0 0 10 10" aria-hidden="true">
            <circle cx="5" cy="5" r="4.6"/>
            <path d="M0.6 5 H9.4 M5 0.4 Q2.6 5 5 9.6 M5 0.4 Q7.4 5 5 9.6" stroke="#fff" stroke-width="0.8" fill="none"/>
          </svg>
          www.brivoterna-example.com
        </li>
        <li class="contact__item">
          <svg class="contact__icon" viewBox="0 0 10 10" aria-hidden="true">
            <rect x="0.3" y="2" width="9.4" height="6.4"/>
            <path d="M0.6 2.3 L5 5.8 L9.4 2.3" stroke="#fff" stroke-width="0.8" fill="none"/>
          </svg>
          teodoro.vinsquel@brivoterna-example.com
        </li>
      </ul>
    </div>
  </section>
</body>
</html>
```